New Business Card Design for Manufacturing

We are an engineering/manufacturing company that offers Advanced machining/assembly/engineering services, as well as innovative products for the heavy duty engine cooling markets.

We are looking to get a new business card designed that is clean and modern looking, but still fits the wide range of technical/skilled work we do.

- We hope to use this design as the base for other design work in new Presentations, web, and print work.

Industry/Entity Type

Engineering

Contact Information for Business Card

Our preferred color of blue is (RGB) 22/71/159 but can vary slightly from that color. Our content will be our Logo and full company name (Vantrell Forge Works, Inc.), company address, name, job title, phone number with extension, cell number, fax number, website, and email address on the cards.
We'd like the full company name next to the logo, but we are open to other interpretations of that layout.
Preferably, we would like the back side to be clean with just our logo, and the front to contain all of the contact information.

Colors
2f74b4
0355a3
85abd2

Requirements
Must have
• - Logo, company name, needed content - We are open to interpretation beyond that.
• - Standard size business card.
• - Horizontal orientation.
• - Enough space for lengthy names / job titles (for example, a job title could read "Directory of Human Resources" or "V.P. of Governmental Affairs"). We need this to look clean, whether the title be short (CEO) or long (as described above).

```html
<!DOCTYPE html>
<html lang="en">
<head>
<meta charset="utf-8">
<title>Vantrell Forge Works – Business Card</title>
<link rel="stylesheet" href="https://fonts.googleapis.com/css2?family=Roboto:wght@400;700;900&family=Roboto+Condensed:wght@500&display=swap">
<style>
  :root {
    --brand-blue: #0f51a0;
    --card-white: #f2f2f2;
    --card-grey: #7b8187;
    --tag-grey: #6d7278;
    --text-light: #ffffff;
    --backdrop: #e6e3de;
  }
  * { margin: 0; padding: 0; box-sizing: border-box; }
  html, body {
    width: 1200px; height: 960px; overflow: hidden;
    background: var(--backdrop);
    font-family: "Roboto", sans-serif;
  }
  .card {
    position: absolute;
    width: 600px;
    border-radius: 22px;
    overflow: hidden;
  }
  .card--front { left: 302px; top: 128px; height: 344px; background: var(--card-white); }
  .card--back  { left: 298px; top: 488px; height: 342px; background: var(--card-grey); }

  .front-band { position: absolute; left: 0; top: 0; }

  .contact { position: absolute; left: 43px; top: 84px; color: var(--text-light); }
  .contact__name {
    font-family: "Roboto Condensed", sans-serif;
    font-weight: 500; font-size: 25px; line-height: 30px; letter-spacing: 0.3px;
  }
  .contact__title { font-size: 14.5px; line-height: 18px; margin-top: 2px; }
  .contact__address { font-size: 14.5px; line-height: 18px; margin-top: 10px; }
  .contact__list { list-style: none; margin-top: 10px; }
  .contact__item {
    display: flex; align-items: center;
    font-size: 14.5px; line-height: 19px;
  }
  .contact__icon { width: 13px; height: 13px; margin-right: 8px; flex: none; }

  .wordmark {
    position: absolute;
    font-family: "Roboto", sans-serif;
    font-weight: 900; font-size: 46px; line-height: 1; letter-spacing: 0.5px;
  }
  .tagline {
    position: absolute;
    font-family: "Roboto", sans-serif;
    font-weight: 700; font-size: 13px; letter-spacing: 0.2px; text-transform: uppercase;
  }
  .card--front .wordmark { left: 322px; top: 152px; color: var(--brand-blue); }
  .card--front .tagline  { left: 323px; top: 212px; color: var(--tag-grey); }

  .card--back .wordmark { left: 107px; top: 134px; color: var(--text-light); }
  .card--back .tagline  { left: 109px; top: 194px; color: var(--text-light); }

  .company-name {
    position: absolute; left: 349px; top: 134px;
    color: var(--text-light);
    font-weight: 700; font-size: 17px; line-height: 20px; text-transform: uppercase;
  }
  .company-name__suffix { font-size: 9px; margin-left: 3px; }
</style>
</head>
<body>

<section class="card card--front" aria-label="Business card front">
  <svg class="front-band" width="600" height="344" viewBox="0 0 600 344" aria-hidden="true">
    <polygon points="0,0 326,0 226,344 0,344" fill="var(--brand-blue)"/>
  </svg>

  <div class="contact">
    <h1 class="contact__name">DANA WHITFIELD</h1>
    <p class="contact__title">V.P. of Governmental Affairs</p>
    <p class="contact__address">4120 Harlow Street<br>Fairbanks, Alaska 34588</p>
    <ul class="contact__list">
      <li class="contact__item">
        <svg class="contact__icon" viewBox="0 0 16 16" aria-hidden="true"><path fill="#fff" d="M3.6 1.2l2.2 2.6c.3.4.3.9 0 1.3L4.6 6.4c.8 1.8 2.2 3.2 4 4l1.3-1.2c.4-.3.9-.3 1.3 0l2.6 2.2c.4.4.4 1 0 1.4l-1.3 1.3C10 16 .1 6 1.9 3.5L3.2 1.2c.1-.2.3-.2.4 0z"/></svg>
        555 214 7730
      </li>
      <li class="contact__item">
        <svg class="contact__icon" viewBox="0 0 16 16" aria-hidden="true"><rect x="4" y="0.8" width="8" height="14.4" rx="1.5" fill="none" stroke="#fff" stroke-width="1.6"/><circle cx="8" cy="12.6" r="0.9" fill="#fff"/></svg>
        555 380 6152
      </li>
      <li class="contact__item">
        <svg class="contact__icon" viewBox="0 0 16 16" aria-hidden="true"><rect x="1" y="4" width="14" height="9" fill="#fff"/><path d="M1 4l7 5 7-5" fill="none" stroke="var(--brand-blue)" stroke-width="1.3"/></svg>
        dana@vantrellforge.com
      </li>
      <li class="contact__item">
        <svg class="contact__icon" viewBox="0 0 16 16" aria-hidden="true"><circle cx="8" cy="8" r="7" fill="#fff"/><path d="M1 8h14M8 1c-2.6 3-2.6 11 0 14M8 1c2.6 3 2.6 11 0 14" fill="none" stroke="var(--brand-blue)" stroke-width="1.1"/></svg>
        www.vantrellforge.com
      </li>
    </ul>
  </div>

  <p class="wordmark">VANTRELL</p>
  <p class="tagline">Built for Tomorrow</p>
</section>

<section class="card card--back" aria-label="Business card back">
  <p class="wordmark">VANTRELL</p>
  <p class="tagline">Built for Tomorrow</p>
  <p class="company-name">Vantrell<br>Forge<br>Works<span class="company-name__suffix">Inc</span></p>
</section>

</body>
</html>
```